"Tidewater Sleeve" - Envelope Package for 3 Small Pamphlets/Tracts

We need a design for an envelope package that will be folded to fit 3 small tracts/pamphlets. The final product will be paper that is simply folded - not glued or stapled. The tracts/pamphlets themselves are the ones that can be found at www.briskcanada.ca/literature - they don't need to be designed as we already have them in print. We just want a package/envelope to put them in so we can hand them out in a creative way.

We are looking for a few different ideas to choose from - which is why we are coming to you! Attached is a design brief that outlines the desired format and pictures of mocked-finished product. Also attached is the "G" (KELVORA logo). One of the pictures will provide you with the final product measurement in millimetres. You will have to add safety margins for full bleed to send to the printer. This needs to be designed in Photoshop or Illustrator. Photoshop is preferred.

Although I like the white background because it looks clean, please also provide a darker background to see if the "wallet" effect would work. (I am talking about the outside of the package. the inside should remain white.)

I like the concept of the icons for body and mind, but the icon for "spirit" should be something like a generic sunrise, sunset or peaceful lake.

You will notice that there are "folding" numbers inside the attached mockup picture. We would like them to be nicely designed on the final product so that people know how to fold the envelope, but those numbers should be hidden behind the flaps/pamphlets once the 3 pamphlets are in and the product is fully folded. We would also like to have light grey dotted lines to know where to fold on the inside of the package.

On the centre back panel is where you have the question that states "Know someone who needs healing?"

```html
<!DOCTYPE html>
<html lang="en">
<head>
<meta charset="utf-8">
<title>Tidewater Sleeve – Outside Dieline</title>
<link href="https://fonts.googleapis.com/css2?family=Montserrat:wght@200;800&display=swap" rel="stylesheet">
<style>
  :root {
    --paper: #ffffff;
    --sleeve: #333333;
    --accent: #5cf000;
    --ink-light: #ffffff;
    --cut: #e0413b;
    --crop: #1a1a1a;
  }
  html, body {
    margin: 0;
    padding: 0;
    width: 1200px;
    height: 861px;
    overflow: hidden;
    background: var(--paper);
  }
  .dieline { display: block; width: 1200px; height: 861px; }
  .panel { fill: var(--sleeve); }
  .cut-edge { stroke: var(--cut); stroke-width: 1.5; fill: none; }
  .crop-mark { stroke: var(--crop); stroke-width: 2; fill: none; }
  .flap-label {
    font-family: 'Montserrat', sans-serif;
    font-weight: 200;
    font-size: 90px;
    fill: var(--ink-light);
  }
  .headline {
    font-family: 'Montserrat', sans-serif;
    font-weight: 800;
    font-size: 84px;
    fill: var(--accent);
  }
  .headline .light { fill: var(--ink-light); }
  .product-title {
    font-family: 'Montserrat', sans-serif;
    font-weight: 800;
    font-size: 80px;
    fill: var(--ink-light);
  }
  .product-title .accent { fill: var(--accent); }
  .brand-band { fill: var(--accent); }
  .brand-name {
    font-family: 'Montserrat', sans-serif;
    font-weight: 800;
    font-size: 36px;
    fill: var(--ink-light);
  }
</style>
</head>
<body>
<svg class="dieline" viewBox="0 0 2268 1627" width="1200" height="861" xmlns="http://www.w3.org/2000/svg">
  <defs>
    <linearGradient id="tone-body" x1="0" y1="0" x2="0" y2="1">
      <stop offset="0" stop-color="#c9c6e6"/>
      <stop offset="0.55" stop-color="#ffc23a"/>
      <stop offset="0.8" stop-color="#f07a1c"/>
      <stop offset="1" stop-color="#2a2620"/>
    </linearGradient>
    <radialGradient id="tone-mind" cx="0.5" cy="0.45" r="0.6">
      <stop offset="0" stop-color="#e8604a"/>
      <stop offset="0.45" stop-color="#2f6cf0"/>
      <stop offset="1" stop-color="#0b1f8a"/>
    </radialGradient>
    <linearGradient id="tone-spirit" x1="0" y1="0" x2="0" y2="1">
      <stop offset="0" stop-color="#8fb2d9"/>
      <stop offset="0.45" stop-color="#e7b48c"/>
      <stop offset="0.7" stop-color="#506b8c"/>
      <stop offset="1" stop-color="#14202e"/>
    </linearGradient>
  </defs>

  <g class="crop-marks">
    <path class="crop-mark" d="M298 210V265H243M243 410H298"/>
    <path class="crop-mark" d="M857 210V265M1416 210V265"/>
    <path class="crop-mark" d="M1960 210V265H2015M2015 410H1960"/>
    <path class="crop-mark" d="M98 1107H153M98 1215H153M2105 1107H2160M2105 1215H2160"/>
    <path class="crop-mark" d="M243 1360H298V1415M857 1360V1415M1416 1360V1415M2015 1360H1960V1415"/>
  </g>

  <g class="panel-body">
    <path class="panel" d="M338 265H845L857 405V1220L845 1360H338L299 1215H153V1107H299V410Z"/>
    <path class="cut-edge" d="M299 410L338 265M845 265L857 405M299 1215L338 1360M845 1360L857 1220"/>
    <text class="flap-label" text-anchor="middle" transform="rotate(180 595 335)" x="595" y="366">Body</text>
    <rect x="521" y="1242" width="94" height="94" rx="12" fill="url(#tone-body)" transform="rotate(180 568 1289)" role="img" aria-label="Body icon: runner against a sunset"/>
  </g>

  <g class="panel-mind">
    <rect class="panel" x="858" y="265" width="558" height="1095"/>
    <text class="flap-label" text-anchor="middle" transform="rotate(180 1137 335)" x="1137" y="366">Mind</text>
    <text class="headline" text-anchor="middle" x="1137">
      <tspan x="1137" y="624">Know</tspan>
      <tspan x="1137" y="706">someone</tspan>
      <tspan x="1137" y="788">who</tspan>
      <tspan x="1137" y="870">needs</tspan>
      <tspan class="light" x="1137" y="953">Healing?</tspan>
    </text>
    <rect x="908" y="1052" width="117" height="117" rx="14" fill="url(#tone-body)" role="img" aria-label="Body icon: runner against a sunset"/>
    <rect x="1076" y="1052" width="117" height="117" rx="14" fill="url(#tone-mind)" role="img" aria-label="Mind icon: glowing brain in a head profile"/>
    <rect x="1244" y="1052" width="117" height="117" rx="14" fill="url(#tone-spirit)" role="img" aria-label="Spirit icon: peaceful mountain lake at sunrise"/>
    <rect x="1090" y="1242" width="94" height="94" rx="12" fill="url(#tone-mind)" transform="rotate(180 1137 1289)" role="img" aria-label="Mind icon: glowing brain in a head profile"/>
  </g>

  <g class="panel-spirit">
    <path class="panel" d="M1431 265H1921L1960 410V1107H2105V1215H1960L1921 1360H1431L1416 1215V410Z"/>
    <path class="cut-edge" d="M1416 410L1431 265M1921 265L1960 410M1416 1215L1431 1360M1921 1360L1960 1215"/>
    <text class="flap-label" text-anchor="middle" transform="rotate(180 1692 335)" x="1692" y="366">Spirit</text>
    <rect class="brand-band" x="1416" y="452" width="230" height="96"/>
    <text class="brand-name" text-anchor="end" x="1630" y="513">KELVORA</text>
    <text class="product-title" text-anchor="middle">
      <tspan x="1690" y="782">Tidewater</tspan>
      <tspan class="accent" x="1690" y="863">Sleeve</tspan>
    </text>
    <rect x="1460" y="1052" width="117" height="117" rx="14" fill="url(#tone-body)" role="img" aria-label="Body icon: runner against a sunset"/>
    <rect x="1628" y="1052" width="117" height="117" rx="14" fill="url(#tone-mind)" role="img" aria-label="Mind icon: glowing brain in a head profile"/>
    <rect x="1796" y="1052" width="117" height="117" rx="14" fill="url(#tone-spirit)" role="img" aria-label="Spirit icon: peaceful mountain lake at sunrise"/>
    <rect x="1639" y="1242" width="94" height="94" rx="12" fill="url(#tone-spirit)" transform="rotate(180 1686 1289)" role="img" aria-label="Spirit icon: peaceful mountain lake at sunrise"/>
  </g>
</svg>
</body>
</html>
```